tinyTally Resource Book - 10 maths tasks to do outside

I need a 22 (11 pages back to back) page A6 sized book produced to standard for submission to professional printer. Needs to be as .pdf file showing guide lines and allowances for colour bleed. I have text already written and submitted as attachment in a Word file with margins set to A6 size. The theme of the materials is "Nature Play" so using lots of pictures from nature (Australia preferably) and showing lots of patterns in nature (rocks, leaves, flower petals etc). Some of the tasks refer to specific activities, such as "shadows" and "floating" so would be great to illustrate appropriately. The big emphasis is on learning outside the classroom, getting kids to engage actively with nature. I would like to see the pages as full colour - so not white background. The book itself will be spiral bound along the top edge so a margin of at least 1cm will be required at the top of each page (or the bottom of even numbered pages). Book will be printed on plastic laminated matte paper for outdoor use. Font size needs to be big enough to read. Fonts sizes, alignments and page numbers are all different at the moment and need to be standardised. One photo is included in a page as a sample if you can use it, otherwise disregard. Logo for Wattlebrook Numeracy Guild is also included to have as part of the acknowledgements at the back of the book.

Target Market(s)

Book is for early childhood and preschool teachers.

Industry/Entity Type

Education

Font styles to use
Sans Serif

Requirements
Must have
• Colour and appeal.
Nice to have
• Use of natural colours instead of bright catchy colours but that is your call.
Should not have
• American spelling

```html
<!DOCTYPE html>
<html lang="en-AU">
<head>
<meta charset="utf-8">
<title>Rolling – Maths Task 9</title>
<link rel="stylesheet" href="https://fonts.googleapis.com/css2?family=Nunito+Sans:ital,wght@0,800;0,900;1,800&family=Didact+Gothic&display=swap">
<style>
  :root {
    --paper: #ffffff;
    --lawn-top: #6f8d5c;
    --lawn-mid: #5c9f45;
    --lawn-low: #4a8f34;
    --ink-blue: #2d3a92;
    --ink-body: #2c3535;
    --bullet-red: #d8282b;
    --trim: #3a3a3a;
  }
  * { margin: 0; padding: 0; box-sizing: border-box; }
  html, body { width: 889px; height: 1200px; overflow: hidden; background: var(--paper); }
  .page { position: relative; width: 889px; height: 1200px; }

  .trim-marks { position: absolute; inset: 0; }

  .backdrop {
    position: absolute; left: 52px; top: 52px; width: 784px; height: 1096px;
    background: linear-gradient(180deg, var(--lawn-top) 0%, #7a9b68 12%, var(--lawn-mid) 28%, var(--lawn-low) 100%);
  }

  .task-title {
    position: absolute; left: 0; width: 889px; top: 104px; text-align: center;
    font: 900 54px/1 "Nunito Sans", sans-serif; color: var(--ink-blue);
    -webkit-text-stroke: 2px #fff; paint-order: stroke fill;
  }
  .outcome {
    position: absolute; left: 0; width: 889px; top: 160px; text-align: center;
    font: 900 33px/38px "Nunito Sans", sans-serif; color: var(--ink-blue);
    -webkit-text-stroke: 1.5px #fff; paint-order: stroke fill;
  }
  .lead {
    position: absolute; left: 124px;
    font: italic 800 27px/33px "Nunito Sans", sans-serif; color: var(--ink-blue);
  }
  .body-copy {
    position: absolute; left: 196px;
    font: 30px/39px "Didact Gothic", sans-serif; letter-spacing: 0.3px; color: var(--ink-body);
  }
  .lead-skills { top: 245px; }
  .body-children { top: 378px; }
  .lead-educators { top: 615px; }
  .body-educators { top: 651px; }
  .lead-task { top: 808px; }

  .task-list {
    position: absolute; left: 186px; top: 844px; list-style: none;
    font: 30px/36px "Didact Gothic", sans-serif; letter-spacing: 0.3px; color: var(--ink-body);
  }
  .task-list li { position: relative; padding-left: 32px; }
  .task-list li::before {
    content: ""; position: absolute; left: 2px; top: 12px; width: 14px; height: 14px;
    background: var(--bullet-red); transform: rotate(45deg);
  }

  .placeholder {
    position: absolute; border-radius: 6px;
    background: linear-gradient(160deg, #8aa86e, #6f8f58);
  }
  .placeholder-ball { left: 606px; top: 764px; width: 98px; height: 96px; }
  .placeholder-stacker { left: 678px; top: 832px; width: 102px; height: 150px; }
  .placeholder-stone { left: 636px; top: 986px; width: 126px; height: 70px; }
</style>
</head>
<body>
<main class="page">
  <div class="backdrop" role="img" aria-label="Photograph of a sunny green lawn with young trees and a brick building behind"></div>

  <svg class="trim-marks" width="889" height="1200" viewBox="0 0 889 1200" aria-hidden="true">
    <g stroke="var(--trim)" stroke-width="0.8">
      <line x1="52" y1="0" x2="52" y2="42"/><line x1="74" y1="0" x2="74" y2="74"/>
      <line x1="0" y1="52" x2="42" y2="52"/><line x1="0" y1="74" x2="74" y2="74"/>
      <line x1="836" y1="0" x2="836" y2="42"/><line x1="814" y1="0" x2="814" y2="74"/>
      <line x1="847" y1="52" x2="889" y2="52"/><line x1="814" y1="74" x2="889" y2="74"/>
      <line x1="52" y1="1158" x2="52" y2="1200"/><line x1="74" y1="1126" x2="74" y2="1200"/>
      <line x1="0" y1="1148" x2="42" y2="1148"/><line x1="0" y1="1126" x2="74" y2="1126"/>
      <line x1="836" y1="1158" x2="836" y2="1200"/><line x1="814" y1="1126" x2="814" y2="1200"/>
      <line x1="847" y1="1148" x2="889" y2="1148"/><line x1="814" y1="1126" x2="889" y2="1126"/>
    </g>
  </svg>

  <h1 class="task-title">9. Rolling</h1>
  <h2 class="outcome">EYLF – Outcome 4: Children are<br>confident and involved learners</h2>

  <p class="lead lead-skills">Children develop a range of skills and processes<br>such as problem solving, inquiry, experimenta-<br>tion, hypothesising, researching and investigat-<br>ing when they...</p>
  <p class="body-copy body-children">make predictions and generalisations<br>about their daily activities, aspects of the<br>natural world and environments, using<br>patterns they generate or identify and<br>communicate these using mathematical<br>language and symbols</p>

  <p class="lead lead-educators">Educators promote this learning when they...</p>
  <p class="body-copy body-educators">provide opportunities for involvement in<br>experiences that support the investigation<br>of ideas, complex concepts and thinking,<br>reasoning and hypothesizing</p>

  <p class="lead lead-task">This task provides an opportunity to:</p>
  <ul class="task-list">
    <li>explore the concepts of<br>“speed” and “distance”</li>
    <li>make predictions and test them</li>
    <li>repeat a task and record results</li>
    <li>reflect on variations in results<br>from testing</li>
  </ul>

  <div class="placeholder placeholder-ball" role="img" aria-label="Illustration of a striped beach ball"></div>
  <div class="placeholder placeholder-stacker" role="img" aria-label="Illustration of a coloured ring stacking toy"></div>
  <div class="placeholder placeholder-stone" role="img" aria-label="Photograph of a smooth brown rock"></div>
</main>
</body>
</html>
```